Calvanto Group Real Estate Company business cards

New business card design, we are generally happy with the basic layout of the existing front of business card, (feel free to change) but require a head shot photo on the back side.

http://www.calvanto.com.au/

Attached logos, and existing business card

------------------------------

Target Market(s)

Real estate

Industry/Entity Type

Real Estate

Contact Information for Business Card

Standard size double sided

Font styles to use
Other font styles liked:
• Futura

Requirements
Must have
• Photo head shot on the back side
Nice to have
• yes
Should not have
• No

```html
<!DOCTYPE html>
<html lang="en">
<head>
<meta charset="utf-8">
<title>Calvanto Group – Business Cards</title>
<link rel="stylesheet" href="https://fonts.googleapis.com/css2?family=Gelasio:wght@400;600&display=swap">
<style>
  :root {
    --bg: #2a2a2a;
    --paper: #ffffff;
    --paper-shade: #eeeeee;
    --purple: #2e1a63;
    --orange: #f0901c;
    --grey: #c8c8c8;
    --ink-light: #e9e6f2;
    --serif: "Gelasio", Georgia, serif;
  }
  * { box-sizing: border-box; margin: 0; padding: 0; }
  html, body { width: 1200px; height: 873px; overflow: hidden; }
  body {
    background: var(--bg);
    display: flex;
    align-items: center;
    justify-content: center;
    gap: 40px;
    font-family: var(--serif);
  }
  .card {
    position: relative;
    width: 540px;
    height: 330px;
    background: linear-gradient(180deg, var(--paper) 0%, var(--paper-shade) 100%);
    overflow: hidden;
    box-shadow: 0 10px 30px rgba(0,0,0,.5);
  }
  .card__wave { position: absolute; inset: 0; width: 100%; height: 100%; }
  .wave-orange { fill: var(--orange); }
  .wave-purple { fill: var(--purple); }

  /* Front */
  .welcome {
    position: absolute;
    top: 82px;
    left: 0;
    right: 0;
    text-align: center;
  }
  .welcome__title { color: var(--orange); font-size: 25px; font-weight: 400; }
  .welcome__tagline { color: var(--purple); font-size: 21px; font-weight: 400; margin-top: 4px; opacity: .85; }
  .brand {
    position: absolute;
    font-family: var(--serif);
    font-weight: 600;
  }
  .brand--front { left: 30px; bottom: 26px; font-size: 32px; color: var(--ink-light); }

  /* Back */
  .brand--back { left: 32px; top: 52px; font-size: 34px; color: var(--purple); }
  .headshot {
    position: absolute;
    left: 365px;
    top: 58px;
    width: 160px;
    height: 160px;
    border-radius: 50%;
    border: 7px solid var(--grey);
    background: radial-gradient(circle at 50% 40%, #dcdcdc 0%, #b9b9b9 55%, #3a3f52 100%);
  }
  .details {
    position: absolute;
    left: 32px;
    bottom: 14px;
    display: flex;
    flex-direction: column;
    gap: 10px;
    color: var(--paper);
  }
  .person__name { font-size: 22px; line-height: 26px; font-weight: 400; color: var(--ink-light); }
  .person__role { font-size: 13px; line-height: 16px; color: var(--ink-light); }
  .contact {
    list-style: none;
    font-size: 13px;
    line-height: 19px;
  }
  .contact__item { display: flex; align-items: center; gap: 8px; }
  .contact__icon { width: 11px; height: 11px; flex: none; }
  .contact__icon * { fill: none; stroke: var(--orange); stroke-width: 1.6; }
  .social {
    position: absolute;
    right: 50px;
    top: 238px;
    display: flex;
    gap: 5px;
  }
  .social__tile { width: 12px; height: 12px; background: var(--grey); border-radius: 2px; }
</style>
</head>
<body>

  <section class="card card--front" aria-label="Card front">
    <svg class="card__wave" viewBox="0 0 540 330" preserveAspectRatio="none" aria-hidden="true">
      <path class="wave-orange" d="M0,250 C150,200 300,190 400,150 C460,125 510,95 540,80 L540,330 L0,330Z"/>
      <path class="wave-purple" d="M0,272 C160,224 310,214 410,172 C470,148 515,118 540,104 L540,330 L0,330Z"/>
    </svg>
    <div class="welcome">
      <h1 class="welcome__title">Welcome to Calvanto Group!</h1>
      <p class="welcome__tagline">Let us show you property</p>
    </div>
    <div class="brand brand--front">Calvanto Group</div>
  </section>

  <section class="card card--back" aria-label="Card back">
    <svg class="card__wave" viewBox="0 0 540 330" preserveAspectRatio="none" aria-hidden="true">
      <path class="wave-orange" d="M0,185 C120,150 260,148 360,156 C430,161 500,154 540,140 L540,330 L0,330Z"/>
      <path class="wave-purple" d="M0,205 C130,170 260,168 360,174 C440,179 500,172 540,158 L540,330 L0,330Z"/>
    </svg>
    <div class="brand brand--back">Calvanto Group</div>
    <div class="headshot" role="img" aria-label="Head shot photo of the director"></div>
    <div class="social" aria-label="Social links">
      <span class="social__tile"></span>
      <span class="social__tile"></span>
      <span class="social__tile"></span>
    </div>
    <div class="details">
      <div class="person">
        <h2 class="person__name">Daniel Tran</h2>
        <p class="person__role">Director</p>
      </div>
      <ul class="contact">
        <li class="contact__item">
          <svg class="contact__icon" viewBox="0 0 12 12" aria-hidden="true"><rect x="3" y="1" width="6" height="10" rx="1"/></svg>
          0412-555-318
        </li>
        <li class="contact__item">
          <svg class="contact__icon" viewBox="0 0 12 12" aria-hidden="true"><rect x="1" y="2.5" width="10" height="7"/><path d="M1,2.5 L6,7 L11,2.5"/></svg>
          daniel.tran@calvanto.com.au
        </li>
        <li class="contact__item">
          <svg class="contact__icon" viewBox="0 0 12 12" aria-hidden="true"><path d="M5,7 L7,5 M4,5 L2,7 a2,2 0 0 0 3,3 L7,8 M8,7 L10,5 a2,2 0 0 0 -3,-3 L5,4"/></svg>
          www.calvanto.com.au
        </li>
      </ul>
    </div>
  </section>

</body>
</html>
```